Our new beauty salon requires a price list brochure

Our beauty clinic is a medical grade skin care clinic. So our salon is very clinical and professional in appearance. I would like the colours to be similar to our logo design with some nice texture or abstract shapes thrown in.
Pricelist, contact details and logo is attached
I would prefer it to be a 3 fold brochure.

Target Market(s)

Females aged 30-50

Colors
85acd3
cedeed
c4c4c4
5c5c5c
000000
ffffff
eea3c7
f9d9e8
dbdbdb

Requirements
Must have
• easy to read

```html
<!DOCTYPE html>
<html lang="en">
<head>
<meta charset="utf-8">
<title>Luma Aesthetics – Price List</title>
<link href="https://fonts.googleapis.com/css2?family=Montserrat:wght@600;700&family=Lato:wght@300;400&display=swap" rel="stylesheet">
<style>
  :root{
    --pink:#eea3c7;
    --pink-soft:#f4bfd6;
    --blush:#f9d9e8;
    --slate:#555e6c;
    --ink:#3c424e;
    --dots:#9aa0aa;
    --white:#ffffff;
  }
  *{margin:0;padding:0;box-sizing:border-box}
  html,body{width:1200px;height:848px;overflow:hidden;background:var(--white)}
  .brochure{
    position:relative;width:1123px;height:794px;
    transform:scale(1.0686);transform-origin:0 0;
    font-family:"Lato",sans-serif;font-weight:300;color:var(--ink);
    background:var(--white);overflow:hidden;
  }
  .backdrop{
    position:absolute;left:360px;top:0;width:763px;height:794px;
    background:
      radial-gradient(ellipse 320px 360px at 560px 180px, rgba(246,196,196,.75), rgba(246,196,196,0) 70%),
      radial-gradient(ellipse 300px 300px at 420px 620px, rgba(244,190,190,.55), rgba(244,190,190,0) 70%),
      radial-gradient(ellipse 260px 420px at 720px 380px, rgba(250,215,210,.7), rgba(250,215,210,0) 70%),
      linear-gradient(90deg, rgba(255,255,255,1) 0%, rgba(252,232,230,.85) 25%, rgba(249,222,218,.9) 60%, rgba(252,236,234,.9) 100%);
  }
  .section{position:absolute}
  .section-title{
    font-family:"Montserrat",sans-serif;font-weight:700;font-size:11px;
    letter-spacing:1.6px;text-transform:uppercase;
    padding:0 0 5px 20px;border-bottom:1.5px solid var(--blush);
  }
  .section-title.pink{color:var(--pink-soft)}
  .section-title.slate{color:var(--slate)}
  .price-list{position:relative;margin:17px 0 0 20px;list-style:none}
  .price-list::after{
    content:"";position:absolute;left:201px;top:0;bottom:0;
    border-left:1px dotted var(--dots);
  }
  .group{list-style:none;position:relative}
  .group + .group{margin-top:9px;padding-top:9px}
  .group + .group::before{
    content:"";position:absolute;left:-20px;top:0;width:183px;
    border-top:1px dotted var(--dots);
  }
  .item{display:flex;height:18.2px;line-height:18.2px;font-size:10.6px}
  .item .name{width:227px}
  .item .price{white-space:nowrap}
  .item .time{font-style:italic;margin-left:4px}

  .service-row{
    display:flex;align-items:center;height:36px;position:relative;
    border-bottom:1.5px solid var(--blush);
  }
  .service-row .title{
    width:227px;padding-left:18px;
    font-family:"Montserrat",sans-serif;font-weight:700;font-size:11px;letter-spacing:1.5px;color:var(--slate);
  }
  .service-row::after{
    content:"";position:absolute;left:220px;top:8px;height:22px;border-left:1px dotted var(--dots);
  }
  .service-row .price{font-size:10.6px}
  .note{padding:17px 0 0 18px;font-size:10.6px;line-height:14.5px}
  .note em{font-style:italic}

  .brand{position:absolute;left:800px;top:672px;width:180px;text-align:center}
  .brand-name{
    font-family:"Montserrat",sans-serif;font-weight:600;font-size:17px;letter-spacing:3px;color:#4b5563;
  }
  .web{position:absolute;left:808px;top:729px;font-family:"Montserrat",sans-serif;font-weight:700;font-size:17px;color:#4b5563}
</style>
</head>
<body>
<main class="brochure">
  <div class="backdrop" role="img" aria-label="Soft-focus beauty portrait photograph in blush pink tones"></div>

  <!-- Column one -->
  <section class="section" style="left:55px;top:110px;width:305px">
    <h2 class="section-title pink">IPL Hair Removal</h2>
    <ul class="price-list">
      <li class="group"><ul>
        <li class="item"><span class="name">Upper lip</span><span class="price">$50</span></li>
        <li class="item"><span class="name">Chin</span><span class="price">$50</span></li>
        <li class="item"><span class="name">Cheeks</span><span class="price">$75</span></li>
        <li class="item"><span class="name">Whole face</span><span class="price">$350</span></li>
      </ul></li>
      <li class="group"><ul>
        <li class="item"><span class="name">Bikini</span><span class="price">$90</span></li>
        <li class="item"><span class="name">G String</span><span class="price">$120</span></li>
        <li class="item"><span class="name">Brazilian</span><span class="price">$150</span></li>
      </ul></li>
      <li class="group"><ul>
        <li class="item"><span class="name">Underarms</span><span class="price">$90</span></li>
        <li class="item"><span class="name">Half arm</span><span class="price">$180</span></li>
        <li class="item"><span class="name">Full arm</span><span class="price">$250</span></li>
        <li class="item"><span class="name">Half leg</span><span class="price">$290</span></li>
        <li class="item"><span class="name">Thighs</span><span class="price">$290</span></li>
        <li class="item"><span class="name">Full leg</span><span class="price">$490</span></li>
      </ul></li>
      <li class="group"><ul>
        <li class="item"><span class="name">Full back</span><span class="price">$350</span></li>
        <li class="item"><span class="name">Shoulders</span><span class="price">$180</span></li>
        <li class="item"><span class="name">Nipples</span><span class="price">$60</span></li>
        <li class="item"><span class="name">Snail trail</span><span class="price">$50</span></li>
        <li class="item"><span class="name">Stomach</span><span class="price">$250</span></li>
        <li class="item"><span class="name">Chest</span><span class="price">$250</span></li>
        <li class="item"><span class="name">Buttocks</span><span class="price">$200</span></li>
      </ul></li>
    </ul>
  </section>

  <section class="section" style="left:55px;top:602px;width:305px">
    <h2 class="section-title pink">IPL Photo Rejuvenation</h2>
    <ul class="price-list">
      <li class="item"><span class="name">Full face</span><span class="price">$350</span></li>
      <li class="item"><span class="name">Neck</span><span class="price">$200</span></li>
      <li class="item"><span class="name">Face, neck ad décolletage</span><span class="price">$450</span></li>
      <li class="item"><span class="name">Spot Treatment</span><span class="price">$50</span></li>
    </ul>
  </section>

  <!-- Column two -->
  <section class="section" style="left:433px;top:110px;width:305px">
    <h2 class="section-title pink">Waxing</h2>
    <ul class="price-list">
      <li class="group"><ul>
        <li class="item"><span class="name">Eyebrow</span><span class="price">$21</span></li>
        <li class="item"><span class="name">Lip</span><span class="price">$15</span></li>
        <li class="item"><span class="name">Chin</span><span class="price">$15</span></li>
        <li class="item"><span class="name">Sides of face</span><span class="price">$20</span></li>
        <li class="item"><span class="name">Underarm</span><span class="price">$20</span></li>
        <li class="item"><span class="name">Forearm</span><span class="price">$25</span></li>
        <li class="item"><span class="name">Full arm</span><span class="price">$35</span></li>
        <li class="item"><span class="name">Lower leg</span><span class="price">$30</span></li>
        <li class="item"><span class="name">Upper leg</span><span class="price">$30</span></li>
        <li class="item"><span class="name">Full leg</span><span class="price">$50</span></li>
        <li class="item"><span class="name">Inner thigh</span><span class="price">$10</span></li>
        <li class="item"><span class="name">Snail trail</span><span class="price">$10</span></li>
        <li class="item"><span class="name">Bikini</span><span class="price">$30</span></li>
        <li class="item"><span class="name">G String</span><span class="price">$40</span></li>
        <li class="item"><span class="name">Brazilian</span><span class="price">$50</span></li>
      </ul></li>
      <li class="group"><ul>
        <li class="item"><span class="name">Eyebrow wax and Lip wax</span><span class="price">$30</span></li>
        <li class="item"><span class="name">Eyebrow, lip and chin wax</span><span class="price">$45</span></li>
      </ul></li>
    </ul>
  </section>

  <section class="section" style="left:433px;top:511px;width:305px">
    <h2 class="section-title pink">Mens Waxing</h2>
    <ul class="price-list">
      <li class="item"><span class="name">Mono brow</span><span class="price">$5</span></li>
      <li class="item"><span class="name">Eyebrow</span><span class="price">$21</span></li>
      <li class="item"><span class="name">Neck</span><span class="price">$20</span></li>
      <li class="item"><span class="name">Full back</span><span class="price">$45</span></li>
      <li class="item"><span class="name">Chest and Abdomen</span><span class="price">$45</span></li>
    </ul>
  </section>

  <!-- Column three -->
  <section class="section" style="left:790px;top:110px;width:303px">
    <h2 class="section-title slate" style="padding-left:18px">Tinting</h2>
    <ul class="price-list" style="margin-left:18px">
      <li class="group"><ul>
        <li class="item"><span class="name">Eyelash Tint</span><span class="price">$25</span></li>
        <li class="item"><span class="name">Lash Lift and Tint</span><span class="price">$80</span></li>
      </ul></li>
      <li class="group"><ul>
        <li class="item"><span class="name">Henna eyebrows and wax</span><span class="price">$80</span></li>
        <li class="item"><span class="name">Eyelash Tint and brow wax</span><span class="price">$40</span></li>
      </ul></li>
    </ul>
  </section>

  <section class="section" style="left:790px;top:258px;width:303px">
    <div class="service-row"><span class="title">LUMA MINI FACIAL</span><span class="price">$80<span class="item time">40min</span></span></div>
    <div class="service-row"><span class="title">LUMA DELUXE FACIAL</span><span class="price">$110<span class="item time">1hr</span></span></div>
    <div class="service-row"><span class="title">MICRODERMABRASION</span><span class="price">$125</span></div>
    <div class="service-row"><span class="title">MINI MICRO</span><span class="price">$80</span></div>
  </section>

  <section class="section" style="left:790px;top:437px;width:303px">
    <h2 class="section-title slate" style="padding-left:18px">Wrinkle Relaxers</h2>
    <p class="note">$175 per area (Crows, frown lines, forehead lines) <em>or</em><br>all 3 areas for $450<br>$50 minor areas (Gummy smile, brow lift, bunny lines)</p>
  </section>

  <section class="section" style="left:790px;top:558px;width:303px">
    <h2 class="section-title slate" style="padding-left:18px">Dermal Fillers and Lip Fillers</h2>
    <p class="note">$500 per ml</p>
  </section>

  <div class="brand"><span class="brand-name">LUMA AESTHETICS</span></div>
  <p class="web">lumaaesthetics.com.au</p>
</main>
</body>
</html>
```